TL - business card

Tallow Partners is an insurance brokerage firm, inovative, proactive, vigorous, which aims to become the leader of the insurance brokers in Anfrica. We should like to get some designs which should be avoided also in Gray / Metallic for the Administration and Orange / Blue for the Managers (ike in the picture sent). The Blue / Green logo is not the correct one, but the source of the file. Please adjust the color accordingly for the business cards. 1 / Orange / Blue 2 / Gray / Metallic We want something classic but which is transmitted strenght, inovation, modernity and most of all, rapidity. We want something start-up like, very punchy and catching eye remaining profesional at the same time. Name: Dorian Whitlock Function: Managing Director Address: N ° 17/18 Rua Veloso - R / C 2B Direita - Bairro Mutamba - Luanda Tel: (+244) 947 582 316 Email: dorian.whitlock@tallow-p.example Website: www.tallow-p. example We want classic in the front and creative, colorfull at the back. The cards will be printed in relief, with very high quality of paper.
Insurance Broker
Colors
Designer to choose colors to be used in the design.

```html
<!DOCTYPE html>
<html lang="en">
<head>
<meta charset="utf-8">
<title>Tallow Partners – Business Card</title>
<link href="https://fonts.googleapis.com/css2?family=Lato:wght@400;700;900&display=swap" rel="stylesheet">
<style>
  :root {
    --backdrop: #e6e6e6;
    --brand-blue: #1e9bd3;
    --brand-orange: #f0960f;
    --paper: #fbfbfb;
    --ink: #2b2b2b;
    --rule: #9a9a9a;
    --white: #ffffff;
  }
  * { margin: 0; padding: 0; box-sizing: border-box; }
  html, body {
    width: 1200px; height: 784px; overflow: hidden;
    background: var(--backdrop);
    font-family: "Lato", Arial, sans-serif;
  }
  .canvas {
    position: relative; width: 1200px; height: 784px;
    display: flex; align-items: center; justify-content: center; gap: 40px;
  }
  .card {
    position: relative; width: 540px; height: 309px; overflow: hidden;
    box-shadow: 0 6px 18px rgba(0,0,0,0.12);
  }

  /* Shared lockup: mark stacked above name */
  .brand-lockup { display: flex; flex-direction: column; align-items: center; }
  .brand-dot { border-radius: 50%; flex: none; }
  .brand-name { font-weight: 900; text-transform: uppercase; letter-spacing: 1px; white-space: nowrap; }

  /* Front */
  .card-front { background: var(--brand-blue); display: flex; align-items: center; justify-content: center; }
  .card-front .brand-lockup { gap: 12px; }
  .card-front .brand-dot { width: 64px; height: 64px; background: var(--white); }
  .card-front .brand-name { color: var(--white); font-size: 28px; }

  /* Back */
  .card-back { background: var(--paper); }
  .card-back .brand-lockup { position: absolute; left: 26px; top: 112px; width: 200px; gap: 8px; }
  .card-back .brand-dot { width: 40px; height: 40px; background: var(--brand-orange); }
  .card-back .brand-name { color: var(--brand-orange); font-size: 18px; }

  .contact-block {
    position: absolute; left: 256px; top: 80px;
    border-left: 1px solid var(--rule);
    padding: 6px 0 8px 14px;
  }
  .person-name { color: var(--brand-blue); font-weight: 900; font-size: 18px; letter-spacing: 0.5px; text-transform: uppercase; }
  .person-role { color: var(--ink); font-size: 11px; margin-top: 1px; margin-bottom: 10px; }
  .contact-list { list-style: none; }
  .contact-list li { display: flex; align-items: center; gap: 7px; color: var(--ink); font-size: 11px; line-height: 15px; white-space: nowrap; }
  .contact-list svg { width: 9px; height: 9px; flex: none; }

  .accent-band {
    position: absolute; right: 0; top: 58px; width: 96px; height: 14px;
    background: var(--brand-blue);
  }
  .accent-mark {
    position: absolute; right: 30px; top: 47px; width: 36px; height: 36px;
    border-radius: 50%; background: var(--white); border: 3px solid var(--brand-orange);
  }
  .address-band {
    position: absolute; left: 0; right: 0; bottom: 30px; height: 24px;
    background: var(--brand-blue); color: var(--white);
    font-size: 11px; display: flex; align-items: center; padding-left: 24px;
    white-space: nowrap;
  }
</style>
</head>
<body>
<main class="canvas">

  <section class="card card-front" aria-label="Card front">
    <div class="brand-lockup">
      <span class="brand-dot"></span>
      <span class="brand-name">Tallow Partners</span>
    </div>
  </section>

  <section class="card card-back" aria-label="Card back">
    <div class="accent-band"></div>
    <div class="accent-mark"></div>

    <div class="brand-lockup">
      <span class="brand-dot"></span>
      <span class="brand-name">Tallow Partners</span>
    </div>

    <div class="contact-block">
      <p class="person-name">Dorian Whitlock</p>
      <p class="person-role">Managing Director</p>
      <ul class="contact-list">
        <li>
          <svg viewBox="0 0 10 10" aria-hidden="true"><path d="M2 0.5 L4 2.5 L3 3.8 Q4.5 6 6.2 7 L7.5 6 L9.5 8 L8 9.5 Q3 8.5 0.5 2 Z" fill="var(--brand-orange)"/></svg>
          (+244) 947 582 316
        </li>
        <li>
          <svg viewBox="0 0 10 10" aria-hidden="true"><rect x="0.5" y="2" width="9" height="6.5" fill="var(--brand-orange)"/><path d="M0.5 2 L5 5.6 L9.5 2" fill="none" stroke="var(--white)" stroke-width="0.9"/></svg>
          dorian.whitlock@tallow-p.example
        </li>
        <li>
          <svg viewBox="0 0 10 10" aria-hidden="true"><circle cx="5" cy="5" r="4.5" fill="var(--brand-orange)"/><path d="M0.5 5 H9.5 M5 0.5 V9.5 M5 0.5 Q2 5 5 9.5 M5 0.5 Q8 5 5 9.5" fill="none" stroke="var(--white)" stroke-width="0.6"/></svg>
          www.tallow-p. example
        </li>
      </ul>
    </div>

    <div class="address-band">N ° 17/18 Rua Veloso - R / C 2B Direita - Bairro Mutamba - Luanda</div>
  </section>

</main>
</body>
</html>
```